Locksmith Business Cards

My father-in-law is in need of new business cards for his locksmith business and I need to impress him. Kindly help me out!

You can see the previous business card attached. It is a family run business in North Wales.

No individual names on the cards.

Key Things to Feature:
- The words "Prompt", "Local", "Reliable" (as you can see under the logo on the website)
- 24h Emergency Service
- Covering All of North Wales, the Wirral and Chester
- The color blue
- A key or a lock would be interesting (similar to the ones that come up when you google locksmith business card)

Optional (only if design includes bullet points, like the example below):
https://imgvaultcdn.net/samples/208314/55172/55172_3904821_208314_image.jpg
- Residential / Commercial / Automotive
- Alarms & Cameras
- Key Cutting & Safes

https://www.brynhafod-locksmiths.co.uk/

Industry/Entity Type

Locksmith

Contact Information for Business Card

01632 960 418
07700 900 362
brynhafodlocksmiths@mailvane.com
Brynhafod Locksmiths, The Willow Barn, 7 Tannery Rd., Llandudno LL99 4QX
www.brynhafod-locksmiths.co.uk

Requirements
Must have
• - The words "Prompt", "Local", "Reliable" (as you can see under the logo on the website)
• - 24h Emergency Service
• - Covering All of North Wales, the Wirral and Chester
Nice to have
• - A key or a lock would be interesting (similar to the ones that come up when you google locksmith business card)

```html
<!DOCTYPE html>
<html lang="en">
<head>
<meta charset="utf-8">
<title>Brynhafod Locksmiths – Business Card</title>
<link href="https://fonts.googleapis.com/css2?family=Oswald:wght@500&family=Roboto:wght@400;500&display=swap" rel="stylesheet">
<style>
  :root {
    --navy: #252a63;
    --mid-blue: #4a5fa3;
    --ink-blue: #2e3a7e;
    --white: #ffffff;
    --text: #1f2454;
    --backdrop: #e7e8ee;
  }
  * { margin: 0; padding: 0; box-sizing: border-box; }
  html, body { width: 1200px; height: 900px; overflow: hidden; }
  body {
    background: var(--backdrop);
    font-family: "Roboto", Arial, sans-serif;
    position: relative;
  }
  .card {
    position: absolute;
    left: 270px;
    width: 660px;
    height: 380px;
    border-radius: 22px;
    overflow: hidden;
    box-shadow: 0 6px 18px rgba(20, 24, 60, 0.18);
  }
  .card-front { top: 45px; background: var(--white); }
  .card-back { top: 475px; background: var(--navy); }

  .wordmark { display: flex; align-items: center; gap: 12px; }
  .wordmark-square { width: 34px; height: 34px; }
  .wordmark-name {
    font-family: "Oswald", Arial, sans-serif;
    font-weight: 500;
    text-transform: uppercase;
    line-height: 1;
    letter-spacing: 0.5px;
  }

  /* front */
  .front-wordmark { position: absolute; left: 38px; top: 34px; }
  .front-wordmark .wordmark-square { background: var(--navy); }
  .front-wordmark .wordmark-name { color: var(--navy); font-size: 34px; }
  .tagline {
    position: absolute; left: 84px; top: 80px;
    color: var(--text); font-size: 16px; letter-spacing: 0.3px;
  }
  .divider {
    position: absolute; left: 38px; right: 38px; top: 118px;
    height: 1px; background: var(--mid-blue);
  }
  .contact-list {
    position: absolute; left: 38px; top: 134px;
    list-style: none; color: var(--text); font-size: 15px; line-height: 23px;
  }
  .contact-list li { display: flex; align-items: center; gap: 10px; }
  .contact-list svg { width: 13px; height: 13px; fill: var(--mid-blue); flex: none; }
  .coverage {
    position: absolute; right: 38px; top: 138px; text-align: right;
    color: var(--ink-blue); font-size: 15px; line-height: 22px; font-weight: 500;
  }
  .front-wave { position: absolute; left: 0; top: 0; width: 660px; height: 380px; }
  .address {
    position: absolute; right: 40px; bottom: 16px; text-align: right;
    color: var(--white); font-size: 15px; line-height: 21px; font-style: normal;
  }

  /* back */
  .back-wordmark { position: absolute; left: 48px; top: 44px; }
  .back-wordmark .wordmark-square { background: var(--white); width: 44px; height: 44px; }
  .back-wordmark .wordmark-name { color: var(--white); font-size: 40px; }
  .emergency {
    position: absolute; left: 48px; top: 112px;
    color: var(--white); font-size: 26px; letter-spacing: 0.3px;
  }
  .service-list {
    position: absolute; left: 60px; top: 166px;
    list-style: none; color: var(--white); font-size: 21px; line-height: 34px; font-weight: 500;
  }
  .service-list li { display: flex; align-items: center; gap: 14px; }
  .service-list li::before {
    content: ""; width: 10px; height: 10px; border-radius: 50%; background: var(--white);
  }
</style>
</head>
<body>

<section class="card card-front" aria-label="Business card front">
  <svg class="front-wave" viewBox="0 0 660 380" aria-hidden="true">
    <path d="M0,240 C180,300 440,225 660,285 L660,380 L0,380 Z" fill="var(--mid-blue)"/>
    <path d="M0,262 C180,318 440,240 660,292 L660,380 L0,380 Z" fill="var(--white)"/>
    <path d="M0,272 C180,326 440,250 660,298 L660,380 L0,380 Z" fill="var(--navy)"/>
  </svg>

  <div class="wordmark front-wordmark">
    <span class="wordmark-square"></span>
    <span class="wordmark-name">Brynhafod Locksmiths</span>
  </div>
  <p class="tagline">Prompt. Local. Reliable</p>
  <div class="divider"></div>

  <ul class="contact-list">
    <li><svg viewBox="0 0 16 16"><path d="M3 1h3l1.5 4-2 1.3a9 9 0 0 0 4.2 4.2L11 8.5l4 1.5v3c0 1-1 2-2 2A13 13 0 0 1 1 3c0-1 1-2 2-2z"/></svg>01632 960 418</li>
    <li><svg viewBox="0 0 16 16"><path d="M4 0h8a1 1 0 0 1 1 1v14a1 1 0 0 1-1 1H4a1 1 0 0 1-1-1V1a1 1 0 0 1 1-1zm1 2v10h6V2z"/></svg>07700 900 362</li>
    <li><svg viewBox="0 0 16 16"><path d="M0 3h16v10H0zm1.5 1.2v.3L8 9l6.5-4.5v-.3z"/></svg>brynhafodlocksmiths@mailvane.com</li>
    <li><svg viewBox="0 0 16 16"><path d="M8 0a8 8 0 1 0 0 16A8 8 0 0 0 8 0zm0 1.5c.9 0 2 2 2.3 5.5H5.7C6 3.5 7.1 1.5 8 1.5zM1.6 7h2.6c.1-2 .5-3.6 1.1-4.7A6.5 6.5 0 0 0 1.6 7zm0 2a6.5 6.5 0 0 0 3.7 4.7C4.7 12.6 4.3 11 4.2 9zm4.1 0h4.6c-.3 3.5-1.4 5.5-2.3 5.5S6 12.5 5.7 9zm6.1 0c-.1 2-.5 3.6-1.1 4.7A6.5 6.5 0 0 0 14.4 9zm2.6-2a6.5 6.5 0 0 0-3.7-4.7c.6 1.1 1 2.7 1.1 4.7z"/></svg>www.brynhafod-locksmiths.co.uk</li>
  </ul>

  <p class="coverage">Covering All of North Wales,<br>the Wirral and Chester</p>

  <address class="address">
    Brynhafod Locksmiths,<br>
    The Willow Barn, 7 Tannery Rd.,<br>
    Llandudno LL99 4QX
  </address>
</section>

<section class="card card-back" aria-label="Business card back">
  <div class="wordmark back-wordmark">
    <span class="wordmark-square"></span>
    <span class="wordmark-name">Brynhafod Locksmiths</span>
  </div>
  <p class="emergency">24h Emergency Service</p>
  <ul class="service-list">
    <li>Residential</li>
    <li>Commercial</li>
    <li>Automotive</li>
    <li>Alarms &amp; Cameras</li>
    <li>Key Cutting &amp; Safes</li>
  </ul>
</section>

</body>
</html>
```